The Brandwell Firm

We need a new design for our letterhead and envelopes. We are a personal injury and criminal defense firm so we need something modern and clean, but more on the professional/traditional side. Our new logo has two colors and is attached to the file so we need something that works well with those colors/matches the design. The following information needs to be on the letterhead:
Phone: (555) 214-3370
Fax: (555) 214-5186
Toll-Free: (888) 431-2059
Post Office Box 4721
Millbrook, SC 29555-4721
HarmClaimCounsel.example
PalmettoTrialAdvocates.example

Target Market(s)

Clients, government agencies, other law firms

Industry/Entity Type

Legal

Font styles to use
Sans Serif
Other font styles liked:
• Arial

Colors

Designer to choose colors to be used in the design.

Requirements
Must have
• Must look professional and clean, modern
Nice to have
• I would like to see a design that works with the logo but does not distract from the content that will be printed on it
Should not have
• Too many colors or crazy designs.

```html
<!DOCTYPE html>
<html lang="en">
<head>
<meta charset="utf-8">
<title>The Brandwell Firm — Letterhead &amp; Envelope</title>
<link rel="stylesheet" href="https://fonts.googleapis.com/css2?family=Roboto:wght@400;500;700&display=swap">
<style>
  :root {
    --stage: #676767;
    --paper: #f1f1f1;
    --navy: #2b1f7a;
    --red: #c4262b;
    --body-text: #6e6e6e;
    --flap-start: #2e1a6e;
    --flap-end: #c0282a;
  }
  * { box-sizing: border-box; margin: 0; padding: 0; }
  html, body { width: 1200px; height: 837px; overflow: hidden; }
  body {
    background: var(--stage);
    font-family: "Roboto", Arial, sans-serif;
    position: relative;
  }
  .sheet {
    position: absolute;
    background: var(--paper);
  }
  .letterhead { left: 120px; top: 122px; width: 417px; height: 590px; }
  .envelope-front { left: 574px; top: 178px; width: 506px; height: 227px; }
  .envelope-back { left: 574px; top: 430px; width: 506px; height: 227px; }

  .brand {
    position: absolute;
    display: flex;
    align-items: center;
    gap: 6px;
  }
  .brand-dot {
    width: 10px; height: 10px; border-radius: 50%;
    background: var(--red);
  }
  .brand-name {
    font-weight: 500;
    font-size: 14px;
    color: var(--navy);
    letter-spacing: 0.2px;
  }
  .letterhead .brand { left: 26px; top: 48px; }
  .envelope-front .brand { left: 35px; top: 57px; }
  .envelope-front .brand-name { font-size: 15px; }

  .letter-body {
    position: absolute;
    left: 26px;
    width: 365px;
    font-size: 6.4px;
    line-height: 9.5px;
    color: var(--body-text);
  }
  .date { top: 131px; }
  .recipient { top: 159px; }
  .recipient strong { font-weight: 700; color: #555; }
  .salutation { top: 216px; }
  .paragraph { text-align: justify; }
  .p1 { top: 235px; }
  .p2 { top: 292px; }
  .p3 { top: 349px; }
  .p4 { top: 387px; }
  .sender-name { top: 453px; font-weight: 700; color: #555; }
  .sender-role { top: 491px; }
  .signature-area {
    position: absolute;
    left: 20px; top: 497px;
    width: 95px; height: 18px;
    background: linear-gradient(90deg, rgba(43,31,122,0.18), rgba(43,31,122,0.05));
    border-radius: 2px;
  }

  .contact {
    position: absolute;
    right: 26px;
    text-align: right;
    font-size: 7.4px;
    line-height: 9.7px;
    color: var(--navy);
  }
  .letterhead .contact { top: 522px; }
  .envelope-front .contact { top: 178px; }
  .contact-line { display: flex; justify-content: flex-end; align-items: center; gap: 3px; }
  .icon { width: 6px; height: 6px; flex: none; }

  .flap { position: absolute; left: 0; top: 0; }
  .flap-web {
    position: absolute;
    left: 0; right: 0; top: 34px;
    text-align: center;
    color: #fff;
    font-size: 6px;
    line-height: 7.5px;
    letter-spacing: 1.2px;
  }
</style>
</head>
<body>

<section class="sheet letterhead">
  <div class="brand"><span class="brand-dot"></span><span class="brand-name">The Brandwell Firm</span></div>

  <p class="letter-body date">30/20/2016</p>
  <p class="letter-body recipient"><strong>Mr. XYZ Smith</strong><br>123, Street No. 123,<br>City Name<br>Pincode-123456</p>
  <p class="letter-body salutation">Dear Sir,</p>

  <p class="letter-body paragraph p1">Lorem Ipsum is simply dummy text of the printing and typesetting industry. Lorem Ipsum has been the industry's standard dummy text ever since the 1500s, when an unknown printer took a galley of type and scrambled it to make a type specimen book. It has survived not only five centuries, but also the leap into electronic typesetting, remaining essentially unchanged. It was popularised in the 1960s with the release of Letraset sheets containing Lorem Ipsum passages, and more recently with desktop publishing software like Aldus PageMaker including versions of Lorem Ipsum.</p>
  <p class="letter-body paragraph p2">Lorem Ipsum is simply dummy text of the printing and typesetting industry. Lorem Ipsum has been the industry's standard dummy text ever since the 1500s, when an unknown printer took a galley of type and scrambled it to make a type specimen book. It has survived not only five centuries, but also the leap into electronic typesetting, remaining essentially unchanged. It was popularised in the 1960s with the release of Letraset sheets containing Lorem Ipsum passages, and more recently with desktop publishing software like Aldus PageMaker including versions of Lorem Ipsum.</p>
  <p class="letter-body paragraph p3">Lorem Ipsum is simply dummy text of the printing and typesetting industry. Lorem Ipsum has been the industry's standard dummy text ever since the 1500s, when an unknown printer took a galley of type and scrambled it to make a type specimen book.</p>
  <p class="letter-body paragraph p4">Lorem Ipsum is simply dummy text of the printing and typesetting industry. Lorem Ipsum has been the industry's standard dummy text ever since the 1500s, when an unknown printer took a galley of type and scrambled it to make a type specimen book.</p>

  <p class="letter-body sender-name">Your Name</p>
  <p class="letter-body sender-role">CEO | Owner</p>
  <div class="signature-area" role="img" aria-label="Handwritten signature placeholder"></div>

  <div class="contact">
    <div class="contact-line">(888) 431-2059
      <svg class="icon" viewBox="0 0 10 10"><path d="M2 1l2 2-1 1.5c.8 1.4 1.6 2.2 3 3L7.5 6l2 2-1.5 1.5C4.5 9 1 5.5.5 2.5z" fill="var(--red)"/></svg></div>
    <div class="contact-line">(555) 214-3370
      <svg class="icon" viewBox="0 0 10 10"><rect x="1" y="3" width="8" height="5" fill="var(--red)"/><rect x="3" y="1" width="4" height="2" fill="var(--red)"/></svg>
      (555) 214-5186
      <svg class="icon" viewBox="0 0 10 10"><rect x="1" y="4" width="8" height="5" rx="1" fill="var(--red)"/><rect x="0.5" y="1.5" width="9" height="2" rx="1" fill="var(--red)"/></svg></div>
    <div class="contact-line">Post Office Box 4721 Millbrook, SC 29555-4721
      <svg class="icon" viewBox="0 0 10 10"><rect x="1" y="3" width="7" height="5" fill="var(--red)"/><rect x="8" y="2" width="1" height="3" fill="var(--red)"/></svg></div>
    <div class="contact-line">www.HarmClaimCounsel.example www.PalmettoTrialAdvocates.example
      <svg class="icon" viewBox="0 0 10 10"><circle cx="5" cy="5" r="4" fill="none" stroke="var(--red)" stroke-width="1.4"/><path d="M1 5h8M5 1v8" stroke="var(--red)" stroke-width="1"/></svg></div>
  </div>
</section>

<section class="sheet envelope-front">
  <div class="brand"><span class="brand-dot"></span><span class="brand-name">The Brandwell Firm</span></div>
  <div class="contact">
    <div class="contact-line">(888) 431-2059
      <svg class="icon" viewBox="0 0 10 10"><path d="M2 1l2 2-1 1.5c.8 1.4 1.6 2.2 3 3L7.5 6l2 2-1.5 1.5C4.5 9 1 5.5.5 2.5z" fill="var(--red)"/></svg></div>
    <div class="contact-line">(555) 214-3370
      <svg class="icon" viewBox="0 0 10 10"><rect x="1" y="3" width="8" height="5" fill="var(--red)"/><rect x="3" y="1" width="4" height="2" fill="var(--red)"/></svg>
      (555) 214-5186
      <svg class="icon" viewBox="0 0 10 10"><rect x="1" y="4" width="8" height="5" rx="1" fill="var(--red)"/><rect x="0.5" y="1.5" width="9" height="2" rx="1" fill="var(--red)"/></svg></div>
    <div class="contact-line">Post Office Box 4721 Millbrook, SC 29555-4721
      <svg class="icon" viewBox="0 0 10 10"><rect x="1" y="3" width="7" height="5" fill="var(--red)"/><rect x="8" y="2" width="1" height="3" fill="var(--red)"/></svg></div>
  </div>
</section>

<section class="sheet envelope-back">
  <svg class="flap" width="506" height="82" viewBox="0 0 506 82">
    <defs>
      <linearGradient id="flapGradient" x1="0" x2="1" y1="0" y2="0">
        <stop offset="0" stop-color="var(--flap-start)"/>
        <stop offset="1" stop-color="var(--flap-end)"/>
      </linearGradient>
    </defs>
    <path d="M0 0H506L472 68Q465 81 448 81H58Q41 81 34 68Z" fill="url(#flapGradient)"/>
  </svg>
  <p class="flap-web">www.harmclaimcounsel.example<br>www.palmettotrialadvocates.example</p>
</section>

</body>
</html>
```